Road Construction Company needs business cards

We would like a new business card designed for our business.

We're a road construction company based in Qld, Australia.

Can the business card please have the following information on it.

Name: Warren Halbeck
Position: General Manager
Phone: 0472 915 348
Email: Warren.halbeck@tovrin.com.au
Address: 87 Marrow Ave, Pendlebay, QLD, 4023
Website: www.tovrin.com.au

Visually we'd like the card to be professional and simple.

Attached is our logo.

Our website is www.tovrin.com.au

Target Market(s)

Men aged 25-60

Contact Information for Business Card

As listed in project description

Font styles to use
Serif

Requirements
Must have
• Large logo on back of card

```html
<!DOCTYPE html>
<html lang="en">
<head>
<meta charset="utf-8">
<title>Tovrin Business Card</title>
<link href="https://fonts.googleapis.com/css2?family=Fira+Sans:wght@400;600;700&display=swap" rel="stylesheet">
<style>
  :root {
    --backdrop: #909396;
    --card-blue: #0353a4;
    --accent-blue: #3ea2de;
    --white: #ffffff;
  }
  * { margin: 0; padding: 0; box-sizing: border-box; }
  html, body {
    width: 1200px;
    height: 1200px;
    overflow: hidden;
    background: var(--backdrop);
    font-family: "Fira Sans", sans-serif;
  }
  .card {
    position: absolute;
    width: 635px;
    height: 403px;
    background: var(--card-blue);
    color: var(--white);
  }
  .card-front { left: 155px; top: 151px; }
  .card-back  { left: 373px; top: 672px; }

  .wordmark {
    font-family: "Fira Sans", sans-serif;
    font-weight: 700;
    color: var(--white);
    letter-spacing: 0.04em;
    line-height: 1;
  }
  .card-front .wordmark {
    position: absolute;
    left: 0; right: 0;
    top: 155px;
    text-align: center;
    font-size: 66px;
  }
  .card-back .wordmark {
    position: absolute;
    left: 62px;
    width: 188px;
    top: 184px;
    text-align: center;
    font-size: 32px;
  }

  .divider {
    position: absolute;
    left: 268px;
    top: 121px;
    width: 2px;
    height: 161px;
    background: var(--white);
  }
  .contact-block {
    position: absolute;
    left: 289px;
    top: 118px;
  }
  .person-name {
    font-size: 20px;
    font-weight: 600;
    letter-spacing: 0.01em;
    line-height: 24px;
  }
  .person-role {
    font-size: 16px;
    color: var(--accent-blue);
    line-height: 20px;
  }
  .contact-list {
    list-style: none;
    margin-top: 20px;
  }
  .contact-list li {
    display: flex;
    align-items: center;
    height: 27.5px;
    font-size: 15.5px;
  }
  .contact-list svg {
    width: 16px;
    height: 16px;
    margin-right: 15px;
    fill: var(--accent-blue);
    flex: none;
  }
</style>
</head>
<body>

<section class="card card-front">
  <div class="wordmark">TOVRIN</div>
</section>

<section class="card card-back">
  <div class="wordmark">TOVRIN</div>
  <div class="divider"></div>
  <div class="contact-block">
    <h1 class="person-name">WARREN HALBECK</h1>
    <p class="person-role">General Manager</p>
    <ul class="contact-list">
      <li>
        <svg viewBox="0 0 16 16" aria-hidden="true"><path d="M1 6c0-2 3-3.5 7-3.5S15 4 15 6v1.5h-3.5V6h-7v1.5H1z"/><path d="M4 8h8l2 5H2z"/></svg>
        0472 915 348
      </li>
      <li>
        <svg viewBox="0 0 16 16" aria-hidden="true"><path d="M1 3h14v10H1z M2 4l6 5 6-5" fill="none" stroke="#3ea2de" stroke-width="1.5"/><path d="M1 3h14L8 9z"/></svg>
        Warren.halbeck@tovrin.com.au
      </li>
      <li>
        <svg viewBox="0 0 16 16" aria-hidden="true"><circle cx="8" cy="8" r="6.5" fill="none" stroke="#3ea2de" stroke-width="1.5"/><path d="M1.5 8h13M8 1.5c-3 3.5-3 9.5 0 13M8 1.5c3 3.5 3 9.5 0 13" fill="none" stroke="#3ea2de" stroke-width="1.2"/></svg>
        www.tovrin.com.au
      </li>
      <li>
        <svg viewBox="0 0 16 16" aria-hidden="true"><path d="M8 0.5a5.5 5.5 0 0 1 5.5 5.5c0 4-5.5 9.5-5.5 9.5S2.5 10 2.5 6A5.5 5.5 0 0 1 8 0.5zm0 3a2.5 2.5 0 1 0 0 5 2.5 2.5 0 0 0 0-5z"/></svg>
        87 Marrow Ave, Pendlebay, QLD, 4023
      </li>
    </ul>
  </div>
</section>

</body>
</html>
```